Tallwick Home Services Web Site

Design Web site with 3-4 pages: Home, About Us, Services and Order form / Schedule Appointment (which will likely be link to Method App and Quickbooks integration.)
Services include: Dryer Vent Cleaning, AC Cleaning, Difficult-to-Reach Light Bulb replacement, Wood Repair and Home Maintenance Plans including Fire Safety Checks and Filter Replacement.

Target Market(s)

Luxury Home Owners, Professionals (Dr's/lawyers) and Seniors

Industry/Entity Type

Home Maintenance

Coding

Coded - Design and coding required

Requirements
Must have
• Tagline - Where Home Maintenance is Elementary

```html
<!DOCTYPE html>
<html lang="en">
<head>
<meta charset="utf-8">
<title>Tallwick Home Services</title>
<link href="https://fonts.googleapis.com/css2?family=Josefin+Sans:wght@400;600;700&display=swap" rel="stylesheet">
<style>
:root{
  --gold:#e1a82c;
  --gray:#6b6b6d;
  --ink:#3b3b3d;
  --text:#6f6f72;
  --white:#ffffff;
  --line:#d9d9d9;
}
*{box-sizing:border-box;margin:0;padding:0}
html,body{width:1200px;height:4573px;overflow:hidden}
body{font-family:"Josefin Sans",Arial,sans-serif;color:var(--ink);background:var(--white);position:relative}
.abs{position:absolute}
.btn{position:absolute;display:flex;align-items:center;justify-content:center;border-radius:30px;background:var(--gold);color:var(--white);font-weight:700;text-transform:uppercase;font-size:15px;letter-spacing:.3px}
.photo{position:absolute}
.header{position:absolute;left:0;top:0;width:1200px;height:110px;background:var(--white);z-index:3}
.brand{position:absolute;text-align:center;color:var(--gold);font-weight:700}
.brand-name{font-size:26px;letter-spacing:2px;line-height:1}
.brand-sub{font-size:11px;letter-spacing:1px;color:var(--gray);margin-top:4px}
.brand-dot{width:34px;height:34px;border-radius:50%;background:var(--gold);margin:0 auto 8px}
.nav{position:absolute;top:68px;left:427px;display:flex;gap:48px;font-size:14px;font-weight:600;color:var(--ink)}
.nav .active{border-bottom:3px solid var(--gold);padding-bottom:8px}
.call{position:absolute;top:14px;left:788px;display:flex;align-items:center;gap:10px;font-size:15px;color:var(--ink)}
.ico-circle{width:32px;height:32px;border-radius:50%;background:var(--gold);display:flex;align-items:center;justify-content:center}
.hero{position:absolute;left:0;top:110px;width:1200px;height:675px;background:linear-gradient(90deg,#6a6a6c 0%,#6e6e70 38%,#948c82 55%,#c8bcab 75%,#d6cab9 100%)}
.hero-kicker{position:absolute;left:121px;top:183px;color:var(--white);font-size:20px;letter-spacing:.5px;display:flex;align-items:center;gap:14px}
.hero-kicker span{display:block;width:48px;height:1px;background:var(--white)}
.hero h1{position:absolute;left:121px;top:224px;color:var(--white);font-size:44px;line-height:48px;font-weight:700;text-transform:uppercase}
.rating{position:absolute;left:121px;top:475px;display:flex;gap:14px;color:var(--white);font-size:14px;font-weight:600;align-items:center}
.rating .badge{width:36px;height:36px;border-radius:50%;background:var(--white)}
.stars{color:var(--gold);letter-spacing:2px;font-size:16px}
.sec-title{position:absolute;left:0;width:1200px;text-align:center;font-weight:700;text-transform:uppercase}
.title-rule{position:absolute;height:2px;background:var(--line)}
.svc{position:absolute;width:250px}
.svc h3{font-size:20px;font-weight:700;color:var(--ink);margin-bottom:8px;line-height:26px}
.svc p{font-size:12px;color:var(--text);line-height:16px}
.svc-icon{position:absolute;width:78px;height:78px;border-radius:50%;display:flex;align-items:center;justify-content:center}
.gold{background:var(--gold)}
.grayc{background:var(--gray)}
.about{position:absolute;left:0;top:1674px;width:1200px;height:559px;background:var(--gray);overflow:hidden}
.about h2{position:absolute;left:690px;top:104px;color:var(--white);font-size:37px;line-height:42px;font-weight:700;text-transform:uppercase}
.about p{position:absolute;left:696px;top:234px;width:460px;color:var(--white);font-size:18.5px;line-height:28px}
.outline-btn{position:absolute;left:696px;top:392px;width:184px;height:52px;border:1.5px solid var(--white);border-radius:30px;color:var(--white);font-weight:700;font-size:15px;display:flex;align-items:center;justify-content:center;gap:6px}
.plans{position:absolute;left:0;top:2233px;width:1200px;height:579px;background:linear-gradient(90deg,#dfa62c,#e4ad35)}
.card{position:absolute;top:2496px;width:430px;height:459px;background:var(--white);border:1px solid #e2e2e2;border-radius:6px;box-shadow:0 4px 14px rgba(0,0,0,.08);overflow:hidden}
.card .photo{left:0;top:0;width:100%;height:248px}
.card h3{position:absolute;left:44px;top:290px;font-size:22px;font-weight:700}
.card p{position:absolute;left:42px;top:326px;width:370px;font-size:12.5px;color:var(--text);line-height:20px}
.card .btn{left:36px;top:382px;width:138px;height:40px;background:var(--gray);font-size:11px}
.card-mark{position:absolute;left:0;top:283px;width:4px;height:40px;background:var(--gold)}
.review-card{position:absolute;left:320px;top:3144px;width:686px;height:332px;border:1.5px solid #cfcfcf;border-radius:8px;background:var(--white)}
.review-card h3{position:absolute;left:186px;top:50px;font-size:28px;font-weight:700}
.review-card p{position:absolute;left:190px;top:104px;width:440px;font-size:17px;line-height:23px;color:var(--ink)}
.arrow-btn{position:absolute;top:3514px;width:54px;height:54px;border-radius:50%;background:var(--gold);display:flex;align-items:center;justify-content:center}
.booking{position:absolute;left:0;top:3639px;width:1200px;height:616px;background:linear-gradient(90deg,#6a6a6c 0%,#6d6d6f 45%,#8a8480 62%,#9d948c 80%,#857f7a 100%)}
.booking h2{position:absolute;left:90px;top:124px;color:var(--white);font-size:37px;line-height:42px;font-weight:700;text-transform:uppercase}
.field{position:absolute;height:48px;background:var(--white);border:1px solid #cfcfcf;font-size:13px;color:var(--text);display:flex;align-items:center;gap:8px;padding-left:16px}
.field.tall{align-items:flex-start;padding-top:14px}
.field svg{flex:none}
.footer-nav{position:absolute;top:4337px;display:flex;gap:22px;font-size:14px;font-weight:600;color:var(--ink);align-items:center}
.footer-nav i{display:block;width:5px;height:5px;background:var(--ink)}
.contact{position:absolute;top:4421px;display:flex;gap:14px;align-items:center}
.contact small{display:block;font-size:13px;color:var(--text)}
.contact b{display:block;font-size:15px;font-weight:400;color:var(--ink);margin-top:4px}
.social{position:absolute;top:4426px;left:898px;display:flex;gap:8px}
.social span{width:36px;height:36px;border-radius:50%;background:var(--gray)}
.social span:first-child{background:var(--gold)}
</style>
</head>
<body>

<header class="header">
  <div class="brand" style="left:140px;top:14px;width:184px">
    <div class="brand-dot"></div>
    <div class="brand-name">TALLWICK</div>
    <div class="brand-sub">— HOME SERVICES —</div>
  </div>
  <nav class="nav">
    <span class="active">HOME</span><span>ABOUT US</span><span>SERVICES</span><span>CONTACT</span>
  </nav>
  <div class="call">
    <div class="ico-circle"><svg width="16" height="16" viewBox="0 0 24 24"><path fill="#fff" d="M6.6 10.8a15 15 0 006.6 6.6l2.2-2.2c.3-.3.7-.4 1-.2 1.1.4 2.3.6 3.6.6.6 0 1 .4 1 1V20c0 .6-.4 1-1 1A17 17 0 013 4c0-.6.4-1 1-1h3.5c.6 0 1 .4 1 1 0 1.3.2 2.5.6 3.6.1.3 0 .7-.2 1z"/></svg></div>
    CALL US NOW (+123) 555 0142
  </div>
  <div class="btn" style="left:855px;top:57px;width:229px;height:40px;font-size:13px">Schedule Appointment</div>
</header>

<section class="hero">
  <div class="photo" role="img" aria-label="Technician replacing a ceiling light bulb" style="left:600px;top:0;width:600px;height:675px;background:linear-gradient(90deg,rgba(214,202,185,0) 0%,rgba(214,202,185,.25) 40%,rgba(200,188,172,.35) 100%)"></div>
  <div class="hero-kicker">TALLWICK HOME SERVICES <span></span></div>
  <h1>Where Home<br>Maintenance is<br>Elementary</h1>
  <div class="btn" style="left:118px;top:390px;width:286px;height:56px">Book an Appointment</div>
  <div class="rating">
    <div class="badge"></div>
    <div>4.9 rating from 220 reviews<div class="stars">★★★★★</div></div>
  </div>
</section>

<div class="abs" style="left:584px;top:838px;width:32px;height:3px;background:var(--gold)"></div>
<h2 class="sec-title" style="top:895px;font-size:40px;color:var(--gray)">Our Services</h2>
<div class="title-rule" style="left:525px;top:948px;width:166px"></div>
<div class="abs" style="left:592px;top:946px;width:16px;height:6px;background:var(--gold)"></div>

<svg class="abs" style="left:400px;top:1040px" width="430" height="280" viewBox="0 0 430 280">
  <path d="M8 270 C10 120 100 20 215 18 C330 20 420 120 422 270" fill="none" stroke="#e1a82c" stroke-width="14"/>
</svg>
<div class="photo" role="img" aria-label="Drill repairing a wooden drawer" style="left:425px;top:1082px;width:166px;height:230px;background:linear-gradient(160deg,#d7c9b3,#9a7450)"></div>
<div class="photo" role="img" aria-label="Worker fitting a ceiling light" style="left:612px;top:1082px;width:166px;height:230px;background:linear-gradient(160deg,#e8e8ea,#8b98a8)"></div>
<div class="photo" role="img" aria-label="Gloved hands cleaning a dryer vent" style="left:426px;top:1332px;width:165px;height:164px;background:linear-gradient(160deg,#f1f3f5,#7ea3c9)"></div>
<div class="photo" role="img" aria-label="Technician cleaning an AC filter" style="left:612px;top:1332px;width:166px;height:164px;background:linear-gradient(160deg,#e6e6e6,#d9a35a)"></div>

<div class="title-rule" style="left:107px;top:1313px;width:298px;height:1px"></div>
<div class="title-rule" style="left:825px;top:1313px;width:293px;height:1px"></div>

<div class="svc-icon gold" style="left:302px;top:1090px"><svg width="36" height="36" viewBox="0 0 24 24" fill="none" stroke="#fff" stroke-width="1.6"><path d="M4 20l9-9M14 4l6 6-3 3-6-6zM20 20L9 9M4 4l3 0 0 3"/></svg></div>
<div class="svc" style="left:118px;top:1176px;text-align:right"><h3>Wood Repair</h3><p>Lorem ipsum dolor sit amet, consec-<br>tetur adipiscing elit, sed do eiusmo</p></div>

<div class="svc-icon grayc" style="left:839px;top:1090px"><svg width="36" height="36" viewBox="0 0 24 24" fill="none" stroke="#fff" stroke-width="1.6"><path d="M9 3h6M12 3v5M8 13a4 4 0 108 0 4 4 0 00-8 0zM6 20h12"/></svg></div>
<div class="svc" style="left:853px;top:1176px"><h3>Difficult-to-Reach Light<br>Bulb replacement</h3><p>Lorem ipsum dolor sit amet, consec-<br>tetur adipiscing elit, sed do eiusmo</p></div>

<div class="svc-icon grayc" style="left:296px;top:1342px"><svg width="36" height="36" viewBox="0 0 24 24" fill="none" stroke="#fff" stroke-width="1.6"><rect x="5" y="4" width="14" height="16" rx="2"/><path d="M8 8h8M8 11h8M8 14h8M8 17h8"/></svg></div>
<div class="svc" style="left:118px;top:1428px;text-align:right"><h3>Dryer Vent Cleaning</h3><p>Lorem ipsum dolor sit amet, consec-<br>tetur adipiscing elit, sed do eiusmo</p></div>

<div class="svc-icon gold" style="left:834px;top:1342px"><svg width="36" height="36" viewBox="0 0 24 24" fill="none" stroke="#fff" stroke-width="1.6"><rect x="3" y="5" width="18" height="8" rx="1"/><path d="M6 10h12M8 16v3M12 16v3M16 16v3"/></svg></div>
<div class="svc" style="left:847px;top:1428px"><h3>AC Cleaning</h3><p>Lorem ipsum dolor sit amet, consec-<br>tetur adipiscing elit, sed do eiusmo</p></div>

<div class="btn" style="left:465px;top:1548px;width:284px;height:54px">Book an Appointment</div>

<section class="about">
  <svg class="abs" style="left:0;top:0" width="640" height="559" viewBox="0 0 640 559">
    <path d="M0 0 H480 C580 90 640 230 620 380 C610 450 590 510 570 559 H0Z" fill="#e1a82c"/>
    <path d="M0 0 H460 C560 90 620 230 600 380 C590 450 570 510 550 559 H0Z" fill="#e4e4e6"/>
  </svg>
  <div class="photo" role="img" aria-label="Man replacing a ceiling air filter" style="left:0;top:0;width:600px;height:559px;background:linear-gradient(135deg,rgba(236,236,236,0) 0%,rgba(200,205,215,.45) 45%,rgba(120,130,200,.5) 100%);clip-path:path('M0 0 H460 C560 90 620 230 600 380 C590 450 570 510 550 559 H0Z')"></div>
  <h2>About Tallwick<br>Home Services</h2>
  <p>Lorem ipsum dolor sit amet, consectetur adipisc-ing elit, sed do eiusmod tempor incididunt ut labore et dolore magna aliqua. Quis ipsum sus-pendisse ultrices gravida. Risus commodo viverra maecenas accumsan lacus vel facilisis.</p>
  <div class="outline-btn">LEARN MORE <svg width="10" height="12" viewBox="0 0 10 12"><path d="M2 1l5 5-5 5" fill="none" stroke="#fff" stroke-width="1.6"/></svg></div>
</section>

<section class="plans">
  <div class="abs" style="left:584px;top:80px;width:32px;height:3px;background:var(--white)"></div>
  <h2 class="sec-title" style="top:108px;font-size:34px;color:var(--white)">Home Maintenance Plans</h2>
  <div class="abs" style="left:570px;top:158px;width:60px;height:2px;background:var(--white)"></div>
  <p class="abs" style="left:0;top:180px;width:1200px;text-align:center;color:var(--white);font-size:18px">Lorem ipsum dolor sit amet, consectetur adipiscing elit, sed do eiusmod tempor inci</p>
</section>
<div class="card" style="left:183px">
  <div class="photo" role="img" aria-label="Hands testing a ceiling smoke detector" style="background:linear-gradient(160deg,#f4f4f4,#c9c2bb)"></div>
  <div class="card-mark"></div>
  <h3>Fire Safety Checks</h3>
  <p>Lorem ipsum dolor sit amet, consectetur adipiscing elit,<br>sed do eiusmod tempor incididunt ut labore e</p>
  <div class="btn">Book Now</div>
</div>
<div class="card" style="left:639px">
  <div class="photo" role="img" aria-label="Technician changing an air vent filter" style="background:linear-gradient(160deg,#d9d4cc,#f2f2f2 55%,#4b4f6a)"></div>
  <h3>Filter Replacement</h3>
  <p>Lorem ipsum dolor sit amet, consectetur adipiscing elit,<br>sed do eiusmod tempor incididunt ut labore e</p>
  <div class="btn">Book Now</div>
</div>

<div class="abs" style="left:0;top:3022px;width:1200px;text-align:center;color:var(--gold);font-size:16px">REVIEWS</div>
<h2 class="sec-title" style="top:3046px;font-size:37px;color:var(--ink)">What People Says</h2>
<svg class="abs" style="left:535px;top:3090px" width="130" height="14" viewBox="0 0 130 14"><path d="M2 10 Q65 0 128 10" fill="none" stroke="#e1a82c" stroke-width="3"/></svg>
<div class="review-card">
  <h3>Excellent Service!</h3>
  <p>"Lorem ipsum dolor sit amet, consectetur adipisc-ing elit, sed do eiusmod tempor incididunt ut labore et dolore magna aliqua. Quis ipsum sus-pendisse ultrices gravida. Risus commodo viverra maecenas accumsan lacus vel facilisis"</p>
  <div class="abs stars" style="left:190px;top:234px;font-size:22px">★★★★★</div>
  <div class="abs" style="left:192px;top:274px;font-size:15px;font-weight:700">Mara Ellison</div>
  <div class="abs" style="left:590px;top:250px;font-size:96px;line-height:96px;color:#cfcfcf;font-weight:700">”</div>
</div>
<div class="abs" style="left:183px;top:3168px;width:280px;height:280px;border-radius:50%;background:var(--gold)"></div>
<div class="photo" role="img" aria-label="Smiling customer giving a thumbs up" style="left:193px;top:3168px;width:268px;height:272px;border-radius:50%;background:linear-gradient(160deg,#e9e6e1,#b9b4ad)"></div>
<div class="arrow-btn" style="left:541px"><svg width="22" height="16" viewBox="0 0 22 16"><path d="M20 8H3M9 2L3 8l6 6" fill="none" stroke="#fff" stroke-width="2"/></svg></div>
<div class="arrow-btn" style="left:606px"><svg width="22" height="16" viewBox="0 0 22 16"><path d="M2 8h17M13 2l6 6-6 6" fill="none" stroke="#fff" stroke-width="2"/></svg></div>

<section class="booking">
  <div class="photo" role="img" aria-label="Happy couple booking on a laptop at home" style="left:640px;top:0;width:560px;height:616px;background:linear-gradient(90deg,rgba(150,135,120,0) 0%,rgba(150,135,120,.3) 40%,rgba(120,100,90,.4) 100%)"></div>
  <h2>Book an<br>Appointment</h2>
</section>
<div class="field" style="left:90px;top:3849px;width:236px"><svg width="12" height="12" viewBox="0 0 12 12"><circle cx="6" cy="4" r="2.5" fill="#aaa"/><path d="M1 12c0-3 2-5 5-5s5 2 5 5z" fill="#aaa"/></svg>First name</div>
<div class="field" style="left:335px;top:3849px;width:238px"><svg width="12" height="12" viewBox="0 0 12 12"><circle cx="6" cy="4" r="2.5" fill="#aaa"/><path d="M1 12c0-3 2-5 5-5s5 2 5 5z" fill="#aaa"/></svg>Last name</div>
<div class="field" style="left:90px;top:3907px;width:236px"><svg width="12" height="12" viewBox="0 0 24 24"><path fill="#aaa" d="M6.6 10.8a15 15 0 006.6 6.6l2.2-2.2c.3-.3.7-.4 1-.2 1.1.4 2.3.6 3.6.6.6 0 1 .4 1 1V20c0 .6-.4 1-1 1A17 17 0 013 4c0-.6.4-1 1-1h3.5c.6 0 1 .4 1 1 0 1.3.2 2.5.6 3.6.1.3 0 .7-.2 1z"/></svg>Email address</div>
<div class="field" style="left:335px;top:3907px;width:238px"><svg width="14" height="11" viewBox="0 0 20 16"><rect x="1" y="1" width="18" height="14" rx="2" fill="#aaa"/><path d="M1 2l9 7 9-7" fill="none" stroke="#fff" stroke-width="1.6"/></svg>Phone</div>
<div class="field tall" style="left:90px;top:3965px;width:483px;height:118px"><svg width="13" height="12" viewBox="0 0 13 12"><path d="M1 1h11v7H5l-3 3V8H1z" fill="#aaa"/></svg>Leave Message</div>
<div class="btn" style="left:90px;top:4101px;width:178px;height:52px">Book Now ›</div>

<div class="abs" style="left:498px;top:4207px;width:204px;height:204px;border-radius:50%;background:var(--white)"></div>
<div class="brand" style="left:490px;top:4245px;width:220px">
  <div class="brand-dot"></div>
  <div class="brand-name" style="font-size:30px">TALLWICK</div>
  <div class="brand-sub" style="font-size:14px">— HOME SERVICES —</div>
</div>
<div class="footer-nav" style="left:111px"><span>HOME</span><i></i><span>ABOUT US</span><i></i><span>SERVICES</span></div>
<div class="footer-nav" style="left:745px"><span>WHY US</span><i></i><span>CONTACT</span><i></i><span>BOOK NOW</span></div>
<div class="abs" style="left:102px;top:4402px;width:982px;height:1px;background:var(--line)"></div>
<div class="contact" style="left:125px">
  <div class="ico-circle" style="width:44px;height:44px"><svg width="20" height="20" viewBox="0 0 24 24"><path fill="#fff" d="M6.6 10.8a15 15 0 006.6 6.6l2.2-2.2c.3-.3.7-.4 1-.2 1.1.4 2.3.6 3.6.6.6 0 1 .4 1 1V20c0 .6-.4 1-1 1A17 17 0 013 4c0-.6.4-1 1-1h3.5c.6 0 1 .4 1 1 0 1.3.2 2.5.6 3.6.1.3 0 .7-.2 1z"/></svg></div>
  <div><small>Phone Number</small><b>(+123) 555 0142</b></div>
</div>
<div class="contact" style="left:496px">
  <div class="ico-circle" style="width:44px;height:44px"><svg width="20" height="16" viewBox="0 0 20 16"><rect x="1" y="1" width="18" height="14" rx="2" fill="none" stroke="#fff" stroke-width="1.6"/><path d="M1 2l9 7 9-7" fill="none" stroke="#fff" stroke-width="1.6"/></svg></div>
  <div><small>Email adress</small><b>info@tallwickhomeservices.com</b></div>
</div>
<div class="social"><span></span><span></span><span></span><span></span></div>
<div class="abs" style="left:102px;top:4492px;width:982px;height:1px;background:var(--line)"></div>
<div class="abs" style="left:0;top:4520px;width:1200px;text-align:center;font-size:13px;color:var(--text)">Copyright © 2025 Tallwick Home Services . All Right Reserved</div>
<div class="abs" style="left:976px;top:4509px;width:108px;height:30px;border-radius:16px;background:#e6e6e6;font-size:10px;font-weight:600;color:var(--gray);display:flex;align-items:center;padding-left:14px">GO TO TOP</div>
<div class="abs" style="left:1056px;top:4509px;width:28px;height:30px;border-radius:0 16px 16px 0;background:var(--gray);display:flex;align-items:center;justify-content:center"><svg width="10" height="12" viewBox="0 0 10 12"><path d="M5 11V2M1 5l4-4 4 4" fill="none" stroke="#fff" stroke-width="1.5"/></svg></div>

</body>
</html>
```